Gift voucher for a photo shoot, folding card DIN long (21 x 9.8 cm)

Hello, I'm a professional photographer and need a new design for my gift voucher card for a photo shoot. The design should be applicable to all types of photo shoots (neutral). I prefer a sophisticated design. The folded card should be printed on both sides.
My data should be included: Logo, Address: Moltkener Strße 27, 07548 Gera, Email: fotograf@tobiaswinkel.eu, Website: www.tobiaswinkel.eu Tel.: 0174 / 5839026
Updates

Please design the folding card in DIN long format (105 x 210 mm, landscape format). The card should open horizontally. Please design the front with the words "Gift voucher for you" and my logo. Please make the logo small – the words "Gift voucher" should be in the foreground.
The colors - use elegant gray with gold or white font color.
The inside should contain the words: Photo shoot for ........ worth .....€, as well as my logo.
My contact details should be on the back.

Target Market(s)

Private customer

Colors

Designer to choose only greyscale colors for use in the design.

Requirements
Must have
• Noble appearance, a gift voucher that one likes to give away, words: Gift voucher for you, photo shoot for ..., worth .......€
Nice to have
• Noble appearance of the gift voucher, a gift voucher that you like to give away
Should not have
• no pictures

```html
<!DOCTYPE html>
<html lang="de">
<head>
<meta charset="utf-8">
<title>Geschenkgutschein Fotoshooting – Tobias Winkel Fotograf</title>
<link href="https://fonts.googleapis.com/css2?family=Cinzel:wght@400;600;700&family=Montserrat:wght@400;500&display=swap" rel="stylesheet">
<style>
  :root {
    --stage: #383838;
    --card: #a6a7aa;
    --card-fold: #9c9da0;
    --white: #ffffff;
    --gold-dark: #8a5a1c;
    --gold-mid: #c9972f;
    --gold-light: #f7ea9e;
    --gold-flat: #f3cd6e;
    --ghost: rgba(255,255,255,0.09);
  }
  * { margin: 0; padding: 0; box-sizing: border-box; }
  html, body { width: 1200px; height: 1200px; overflow: hidden; background: var(--stage); }
  .stage { position: relative; width: 1200px; height: 1200px; font-family: 'Montserrat', sans-serif; color: var(--white); }

  .spread { position: absolute; left: 92px; width: 1013px; height: 264px; background: var(--card);
    box-shadow: 0 22px 30px rgba(0,0,0,0.35); overflow: hidden; }
  .spread--outside { top: 293px; }
  .spread--inside { top: 623px; }
  .panel { position: absolute; top: 0; height: 100%; }
  .panel--left { left: 0; width: 512px; }
  .panel--right { left: 512px; width: 501px;
    background: linear-gradient(90deg, var(--card-fold) 0, var(--card) 18px); }

  .abs { position: absolute; }
  .center-x { transform: translateX(-50%); text-align: center; white-space: nowrap; }

  .gold-text { background: linear-gradient(90deg, var(--gold-dark) 0%, var(--gold-mid) 25%, var(--gold-light) 50%, var(--gold-mid) 75%, var(--gold-dark) 100%);
    -webkit-background-clip: text; background-clip: text; color: transparent; }

  .brand { position: absolute; text-align: center; transform: translateX(-50%); white-space: nowrap; }
  .brand__dot { display: block; margin: 0 auto; border: 1.5px solid var(--white); border-radius: 50%; }
  .brand__name { font-family: 'Cinzel', serif; font-weight: 400; color: var(--white); line-height: 1; }
  .brand__role { font-family: 'Montserrat', sans-serif; font-weight: 500; color: var(--white); line-height: 1; }

  .brand--large { left: 256px; top: 19px; }
  .brand--large .brand__dot { width: 46px; height: 46px; margin-bottom: 8px; }
  .brand--large .brand__name { font-size: 20px; letter-spacing: 0.5px; }
  .brand--large .brand__role { font-size: 8px; letter-spacing: 4px; margin-top: 4px; }

  .brand--small { left: 446px; top: 198px; }
  .brand--small .brand__dot { width: 26px; height: 26px; border-width: 1px; margin-bottom: 4px; }
  .brand--small .brand__name { font-size: 12px; }
  .brand--small .brand__role { font-size: 4.5px; letter-spacing: 2px; margin-top: 2px; }

  .contact-icons { left: 256px; top: 166px; display: flex; align-items: center; gap: 7px; color: var(--white); font-size: 9px; }
  .contact-icons svg { width: 9px; height: 9px; }
  .contact-list { left: 256px; top: 186px; list-style: none; font-size: 8.5px; line-height: 16.5px; }

  .title-small { font-family: 'Cinzel', serif; font-weight: 700; font-size: 33px; left: 250px; top: 13px; }
  .title-large { font-family: 'Cinzel', serif; font-weight: 700; font-size: 64px; left: 250px; top: 49px; line-height: 1; }
  .title-sub { font-family: 'Montserrat', sans-serif; font-weight: 500; font-size: 21px; letter-spacing: 3px; color: var(--gold-flat); left: 250px; top: 110px; }

  .camera { position: absolute; left: 6px; width: 68px; height: 66px; }
  .camera--outside { top: 184px; }
  .camera--inside { top: 183px; }

  .ghost-ring { left: 8px; top: 0px; width: 266px; height: 266px; border-radius: 50%; border: 9px solid var(--ghost); }

  .services { left: 330px; top: 38px; list-style: none; }
  .services li { position: relative; padding-left: 14px; font-size: 19px; font-weight: 500; letter-spacing: 2.5px; height: 42px; line-height: 24px; }
  .services li::before { content: ""; position: absolute; left: 0; top: 9px; width: 6px; height: 6px; border-radius: 50%; background: var(--gold-flat); }

  .shoot-title { font-family: 'Cinzel', serif; font-weight: 700; font-size: 35px; left: 250px; top: 17px; line-height: 1; }
  .shoot-for { font-family: 'Montserrat', sans-serif; font-weight: 500; font-size: 21px; letter-spacing: 3px; color: var(--gold-flat); left: 250px; top: 57px; }
  .name-line { left: 41px; top: 134px; width: 408px; height: 2px;
    background: linear-gradient(90deg, var(--gold-dark), var(--gold-light) 50%, var(--gold-dark)); }
  .value { left: 107px; top: 172px; font-size: 16px; font-weight: 500; letter-spacing: 2.5px; white-space: nowrap; }
  .value__dots { letter-spacing: 2px; margin-left: 6px; font-size: 12px; }
  .value__currency { margin-left: 8px; }
  .voucher-no { left: 185px; top: 232px; font-size: 11px; font-weight: 500; letter-spacing: 1px; }
</style>
</head>
<body>
<main class="stage">

  <section class="spread spread--outside" aria-label="Außenseite">
    <div class="panel panel--left">
      <div class="brand brand--large">
        <span class="brand__dot"></span>
        <div class="brand__name">TOBIAS WINKEL</div>
        <div class="brand__role">FOTOGRAF</div>
      </div>
      <div class="abs contact-icons center-x">
        <svg viewBox="0 0 10 10" fill="none" stroke="var(--gold-flat)" stroke-width="1.2"><path d="M2 1l2 2-1 1.2c.6 1.2 1.6 2.2 2.8 2.8L7 6l2 2-1.3 1.2C4.5 9 1 5.5.8 2.3z"/></svg>
        <span>|</span>
        <svg viewBox="0 0 10 10" fill="none" stroke="var(--gold-flat)" stroke-width="0.9"><circle cx="5" cy="5" r="4"/><ellipse cx="5" cy="5" rx="1.8" ry="4"/><path d="M1 5h8"/></svg>
        <span>|</span>
        <svg viewBox="0 0 10 10" fill="var(--gold-flat)"><rect x="0.5" y="2" width="9" height="6.5"/><path d="M0.5 2L5 5.6 9.5 2" stroke="var(--card)" stroke-width="0.8" fill="none"/></svg>
        <span>|</span>
        <svg viewBox="0 0 10 10" fill="none" stroke="var(--gold-flat)" stroke-width="1.1"><circle cx="5" cy="3.6" r="2.3"/><path d="M1.5 9.3h7M5 6v3"/></svg>
      </div>
      <ul class="abs contact-list center-x">
        <li>0174 / 5839026</li>
        <li>www.tobiaswinkel.eu</li>
        <li>fotograf@tobiaswinkel.eu</li>
        <li>Moltkener Strße 27, 07548 Gera</li>
      </ul>
    </div>
    <div class="panel panel--right">
      <div class="abs title-small center-x gold-text">GESCHENK</div>
      <div class="abs title-large center-x gold-text">GUTSCHEIN</div>
      <div class="abs title-sub center-x">FÜR DICH</div>
      <svg class="camera camera--outside" viewBox="0 0 68 66" fill="none" aria-hidden="true">
        <path d="M27 13l3-6 3 4 4-7 2 7 5-3-1 6 5-1" stroke="var(--gold-flat)" stroke-width="2" stroke-linejoin="round"/>
        <path d="M3 26h16l5-6h20l5 6h15v38H3z" stroke="var(--white)" stroke-width="2" stroke-linejoin="round"/>
        <circle cx="34" cy="43" r="13" stroke="var(--white)" stroke-width="2"/>
        <circle cx="34" cy="43" r="9" stroke="var(--white)" stroke-width="2"/>
        <rect x="7" y="22" width="5" height="3" fill="var(--white)"/>
        <circle cx="8" cy="32" r="2" stroke="var(--white)" stroke-width="1.5"/>
      </svg>
      <div class="brand brand--small">
        <span class="brand__dot"></span>
        <div class="brand__name">TOBIAS WINKEL</div>
        <div class="brand__role">FOTOGRAF</div>
      </div>
    </div>
  </section>

  <section class="spread spread--inside" aria-label="Innenseite">
    <div class="panel panel--left">
      <div class="abs ghost-ring" aria-hidden="true"></div>
      <ul class="abs services">
        <li>FAMILIE</li>
        <li>HOCHZEIT</li>
        <li>PORTRAIT</li>
        <li>BUSINESS</li>
        <li>KARRIERE</li>
      </ul>
    </div>
    <div class="panel panel--right">
      <div class="abs shoot-title center-x gold-text">FOTOSHOOTING</div>
      <div class="abs shoot-for center-x">FÜR</div>
      <div class="abs name-line"></div>
      <div class="abs value">IM WERT VON<span class="value__dots">..................</span><span class="value__currency">€</span></div>
      <div class="abs voucher-no">Nr:</div>
      <svg class="camera camera--inside" viewBox="0 0 68 66" fill="none" aria-hidden="true">
        <path d="M27 13l3-6 3 4 4-7 2 7 5-3-1 6 5-1" stroke="var(--gold-flat)" stroke-width="2" stroke-linejoin="round"/>
        <path d="M3 26h16l5-6h20l5 6h15v38H3z" stroke="var(--white)" stroke-width="2" stroke-linejoin="round"/>
        <circle cx="34" cy="43" r="13" stroke="var(--white)" stroke-width="2"/>
        <circle cx="34" cy="43" r="9" stroke="var(--white)" stroke-width="2"/>
        <rect x="7" y="22" width="5" height="3" fill="var(--white)"/>
        <circle cx="8" cy="32" r="2" stroke="var(--white)" stroke-width="1.5"/>
      </svg>
      <div class="brand brand--small">
        <span class="brand__dot"></span>
        <div class="brand__name">TOBIAS WINKEL</div>
        <div class="brand__role">FOTOGRAF</div>
      </div>
    </div>
  </section>

</main>
</body>
</html>
```